Building company buisness cards

We are looking for a sharp modern new look for our business cards.We are a New Zealand based company that specialises in house and land packages.We have attached a photo of the current logo and would like to see if it can be improved somehow if needed.We are open to any colours but we have chosen Black and White at this stage. Feel free to change the font and make the logo smarter looking.Play with the colours and see what looks best.We want a card that looks so good know one will want to throw it away!

Target Market(s)

Building profesonals, home buyers

Industry/Entity Type

Building

Contact Information for Business Card

Garrick Tenwood
0275390628
garrickt@hartvale.co.nz

Font styles to use
Serif
Sans Serif

Colors

Designer to choose colors to be used in the design.

Requirements
Must have
• Just the logo on one side and details on the other
• Clean simple looking card
Nice to have
• Round corners and detail like raised or spot UV
• Something that stands out
Should not have
• To title needed, Director etc

```html
<!DOCTYPE html>
<html lang="en">
<head>
<meta charset="utf-8">
<title>Hartvale Business Cards</title>
<link rel="stylesheet" href="https://fonts.googleapis.com/css2?family=Playfair+Display:wght@700&family=Open+Sans:wght@400;700&display=swap">
<style>
  :root {
    --backdrop: #2a2a2c;
    --card: #ffffff;
    --ink: #111114;
    --muted: #555558;
    --wordmark-font: "Playfair Display", Georgia, serif;
    --text-font: "Open Sans", Arial, sans-serif;
  }
  html, body {
    margin: 0;
    width: 1200px;
    height: 885px;
    overflow: hidden;
    background: var(--backdrop);
  }
  .sheet {
    position: relative;
    width: 1200px;
    height: 885px;
  }
  .card {
    position: absolute;
    width: 540px;
    height: 310px;
    background: var(--card);
    border-radius: 22px;
    overflow: hidden;
  }
  .card--details { left: 90px; top: 120px; }
  .card--brand { left: 570px; top: 455px; }

  .corner-band {
    position: absolute;
    inset: 0;
  }
  .wordmark {
    font-family: var(--wordmark-font);
    font-weight: 700;
    color: var(--ink);
    margin: 0;
    line-height: 1;
  }
  .card--details .wordmark {
    position: absolute;
    right: 34px;
    top: 28px;
    font-size: 44px;
  }
  .contact {
    position: absolute;
    right: 28px;
    top: 150px;
    text-align: right;
    font-family: var(--text-font);
    color: var(--muted);
    font-size: 14px;
    line-height: 21px;
  }
  .contact__name {
    font-weight: 700;
    color: var(--ink);
    font-size: 16px;
    margin-bottom: 3px;
  }
  .contact__row {
    display: flex;
    justify-content: flex-end;
    align-items: center;
    gap: 8px;
  }
  .contact__icon { width: 12px; height: 12px; flex: none; }

  .card--brand .wordmark {
    position: absolute;
    left: 0;
    right: 0;
    top: 112px;
    text-align: center;
    font-size: 60px;
  }
  .card--brand .web {
    position: absolute;
    left: 0;
    right: 0;
    top: 214px;
    margin: 0;
    text-align: center;
    font-family: var(--text-font);
    font-size: 13px;
    letter-spacing: 6px;
    color: var(--muted);
  }
</style>
</head>
<body>
<main class="sheet">
  <section class="card card--details">
    <svg class="corner-band" viewBox="0 0 540 310" aria-hidden="true">
      <path d="M0 110 L0 310 L250 310 Z" fill="var(--ink)"/>
    </svg>
    <p class="wordmark">Hartvale</p>
    <div class="contact">
      <div class="contact__row contact__name">Garrick Tenwood</div>
      <div class="contact__row">0275390628
        <svg class="contact__icon" viewBox="0 0 12 12"><path d="M2 1 L4.5 1 L5.5 3.5 L4 4.6 Q5 7 7.4 8 L8.5 6.5 L11 7.5 L11 10 Q11 11 10 11 Q1 10 1 2 Q1 1 2 1 Z" fill="var(--ink)"/></svg>
      </div>
      <div class="contact__row">garrickt@hartvale.co.nz
        <svg class="contact__icon" viewBox="0 0 12 12"><rect x="0.5" y="2" width="11" height="8" rx="1" fill="var(--ink)"/><path d="M1 2.6 L6 6.6 L11 2.6" stroke="#fff" stroke-width="1" fill="none"/></svg>
      </div>
      <div class="contact__row">www.hartvale.co.nz
        <svg class="contact__icon" viewBox="0 0 12 12"><circle cx="6" cy="6" r="5.5" fill="var(--ink)"/><path d="M0.5 6 H11.5 M6 0.5 Q3 6 6 11.5 M6 0.5 Q9 6 6 11.5" stroke="#fff" stroke-width="0.8" fill="none"/></svg>
      </div>
    </div>
  </section>

  <section class="card card--brand">
    <p class="wordmark">Hartvale</p>
    <p class="web">www.Hartvale.co.nz</p>
  </section>
</main>
</body>
</html>
```